Business Card Design for a Personal Trainer

I need a business card design for my job as a personal trainer. It should have a unique, modern and exclusive design. On the front there should be only my logo with my name and my job. 0162/3819204 Tobias Lendhart Wiesengrundweg 14 80417 Munich Germany The most important contact information is the web adress. it can be bigger than the rest, but its not necessary. The card should be 8,5cmx5,5cm big. Font: Roboto. Colors: black, white, gray, 56c1ff.

```html
<!DOCTYPE html>
<html lang="de">
<head>
<meta charset="utf-8">
<title>Tobias Lendhart – Personal Trainer Visitenkarte</title>
<link href="https://fonts.googleapis.com/css2?family=Roboto:wght@300;400;500&display=swap" rel="stylesheet">
<style>
  :root {
    --stage-light: #ececec;
    --stage-dark: #c9c9c9;
    --card-black: #050505;
    --white: #ffffff;
    --gray: #9a9a9a;
    --accent: #56c1ff;
    --photo-dark: #0b0b0b;
    --photo-mid: #2a2a2a;
  }
  * { box-sizing: border-box; margin: 0; padding: 0; }
  html, body { width: 1200px; height: 864px; overflow: hidden; }
  body {
    font-family: "Roboto", sans-serif;
    background: radial-gradient(ellipse at 50% 40%, var(--stage-light) 0%, var(--stage-dark) 100%);
    position: relative;
  }
  .card {
    position: absolute;
    width: 540px;
    height: 350px;
    background: var(--card-black);
    box-shadow: 0 14px 30px rgba(0,0,0,0.28);
    overflow: hidden;
  }
  /* Contact side */
  .card--contact { left: 45px; top: 257px; }
  .brand {
    position: absolute;
    left: 30px; top: 112px;
    width: 270px;
    text-align: center;
  }
  .brand__name {
    display: inline-flex;
    align-items: center;
    gap: 10px;
    color: var(--white);
    font-weight: 400;
    font-size: 25px;
    letter-spacing: 1.5px;
    text-transform: uppercase;
  }
  .brand__mark { width: 12px; height: 12px; background: var(--white); }
  .brand__job {
    margin-top: 6px;
    color: var(--white);
    font-weight: 300;
    font-size: 11px;
    letter-spacing: 4.5px;
    text-transform: uppercase;
    border-top: 1px solid var(--white);
    border-bottom: 1px solid var(--white);
    display: inline-block;
    padding: 2px 12px;
  }
  .website {
    position: absolute;
    left: 30px; top: 248px;
    width: 270px;
    text-align: center;
    color: var(--accent);
    font-size: 19px;
    font-weight: 400;
    letter-spacing: 0.5px;
  }
  .divider {
    position: absolute;
    left: 318px; top: 88px;
    width: 2px; height: 150px;
    background: var(--accent);
  }
  .contact {
    position: absolute;
    left: 340px; top: 92px;
    color: var(--white);
  }
  .contact__name {
    color: var(--accent);
    font-size: 17px;
    font-weight: 500;
    margin-bottom: 22px;
  }
  .contact__list { list-style: none; font-size: 13.5px; line-height: 1.35; }
  .contact__item { display: flex; align-items: flex-start; gap: 8px; }
  .contact__item svg { flex: none; width: 11px; height: 11px; margin-top: 3px; fill: var(--accent); }
  /* Photo side */
  .card--photo { left: 615px; top: 257px; }
  .photo {
    position: absolute; inset: 0;
    background:
      radial-gradient(ellipse at 28% 48%, #4a4a4a 0%, #232323 28%, transparent 48%),
      linear-gradient(110deg, var(--photo-dark) 0%, var(--photo-mid) 55%, var(--photo-dark) 100%);
  }
  .card--photo .brand { left: 260px; top: 200px; width: 260px; }
  .card--photo .brand__name { font-size: 22px; }
  .card--photo .brand__job { font-size: 10px; letter-spacing: 4px; }
</style>
</head>
<body>
  <section class="card card--contact">
    <div class="brand">
      <div class="brand__name"><span class="brand__mark"></span>Tobias Lendhart</div>
      <div class="brand__job">Personal Trainer</div>
    </div>
    <div class="website">www.lendhart-fit.de</div>
    <div class="divider"></div>
    <div class="contact">
      <div class="contact__name">Tobias Lendhart</div>
      <ul class="contact__list">
        <li class="contact__item">
          <svg viewBox="0 0 24 24"><path d="M6.6 10.8a15.1 15.1 0 0 0 6.6 6.6l2.2-2.2c.3-.3.7-.4 1-.2 1.1.4 2.3.6 3.6.6.6 0 1 .4 1 1V20c0 .6-.4 1-1 1A17 17 0 0 1 3 4c0-.6.4-1 1-1h3.5c.6 0 1 .4 1 1 0 1.3.2 2.5.6 3.6.1.3 0 .7-.2 1z"/></svg>
          <span>0162/3819204</span>
        </li>
        <li class="contact__item">
          <svg viewBox="0 0 24 24"><path d="M2 5h20v14H2z M2 5l10 8 10-8" /></svg>
          <span>kontakt@lendhart-fit.de</span>
        </li>
        <li class="contact__item">
          <svg viewBox="0 0 24 24"><path d="M12 2a7 7 0 0 0-7 7c0 5.2 7 13 7 13s7-7.8 7-13a7 7 0 0 0-7-7zm0 9.5A2.5 2.5 0 1 1 12 6.5a2.5 2.5 0 0 1 0 5z"/></svg>
          <span>Wiesengrundweg 14<br>80417 München</span>
        </li>
      </ul>
    </div>
  </section>

  <section class="card card--photo">
    <div class="photo" role="img" aria-label="Black-and-white photo of the trainer standing with crossed arms in front of a dark gym with a rowing machine"></div>
    <div class="brand">
      <div class="brand__name"><span class="brand__mark"></span>Tobias Lendhart</div>
      <div class="brand__job">Personal Trainer</div>
    </div>
  </section>
</body>
</html>
```